Business card design needed

I would like a one sided black business card with the information provided above. Refer to my website www.brightvolleyracquets.com.au for an example of colors I have used for my site, would like to keep this consistent for my business cards also, I will upload my logo below.

I am a new small business that provides tennis customers with racquet re stringing, tennis strings and accessories.

Industry/Entity Type

Small Business

Contact Information for Business Card

Bright Volley Tennis

Owen Whitby
Managing Director

brightvolleyracquets@mailbox.example
www.brightvolleyracquets.com.au
0491 726 305

Racquet Restringing/Tennis Strings/Accessories

Requirements
Must have
• Must have my logo and card must be black

```html
<!DOCTYPE html>
<html lang="en">
<head>
<meta charset="utf-8">
<title>Bright Volley Tennis – Business Card</title>
<link rel="stylesheet" href="https://fonts.googleapis.com/css2?family=Source+Sans+3:ital,wght@0,400;0,700;1,700&display=swap">
<style>
  :root {
    --page: #5a3d27;
    --card: #000000;
    --lime: #b5d334;
    --navy: #2b4f8c;
    --white: #ffffff;
    --ink: #000000;
  }
  html, body {
    margin: 0;
    width: 1200px;
    height: 750px;
    overflow: hidden;
    background: var(--page);
    font-family: "Source Sans 3", "Myriad Pro", Arial, sans-serif;
  }
  .card {
    position: absolute;
    left: 75px;
    top: 75px;
    width: 1050px;
    height: 597px;
    background: var(--card);
    border-radius: 40px;
    overflow: hidden;
  }
  .brand {
    position: absolute;
    left: 0;
    right: 0;
    top: 150px;
    display: flex;
    justify-content: center;
    align-items: center;
    gap: 22px;
  }
  .brand-dot {
    width: 58px;
    height: 58px;
    border-radius: 50%;
    background: var(--lime);
  }
  .brand-name {
    margin: 0;
    font-size: 60px;
    font-weight: 700;
    color: var(--lime);
    line-height: 1;
    letter-spacing: 1px;
  }
  .services {
    position: absolute;
    left: 0;
    right: 0;
    top: 307px;
    margin: 0;
    padding: 0;
    list-style: none;
    display: flex;
    justify-content: center;
    gap: 20px;
    color: var(--white);
    font-size: 34px;
    line-height: 44px;
  }
  .services li {
    display: flex;
    align-items: center;
  }
  .services li::before {
    content: "";
    width: 9px;
    height: 9px;
    background: var(--white);
    margin-right: 12px;
    margin-top: -6px;
  }
  .rule {
    position: absolute;
    left: 0;
    width: 100%;
    height: 3px;
    background: var(--navy);
  }
  .rule-top { top: 391px; }
  .rule-bottom { top: 496px; }
  .contact-band {
    position: absolute;
    left: 0;
    width: 100%;
    top: 399px;
    height: 93px;
    background: var(--lime);
    color: var(--ink);
  }
  .person-name {
    position: absolute;
    left: 115px;
    top: 16px;
    margin: 0;
    font-size: 34px;
    font-weight: 700;
    line-height: 1;
  }
  .person-role {
    position: absolute;
    left: 115px;
    top: 58px;
    margin: 0;
    font-size: 25px;
    line-height: 1;
  }
  .phone {
    position: absolute;
    left: 680px;
    top: 32px;
    margin: 0;
    font-size: 26px;
    line-height: 1;
  }
  .label {
    font-weight: 700;
    font-style: italic;
  }
  .footer-contacts {
    position: absolute;
    left: 0;
    right: 0;
    top: 533px;
    margin: 0;
    text-align: center;
    color: var(--white);
    font-size: 26px;
    line-height: 34px;
  }
  .divider { margin: 0 12px; }
</style>
</head>
<body>
  <div class="card">
    <div class="brand">
      <span class="brand-dot"></span>
      <h1 class="brand-name">Bright Volley Tennis</h1>
    </div>

    <ul class="services">
      <li>Racquet Restringing</li>
      <li>Tennis Strings</li>
      <li>Accessories</li>
    </ul>

    <div class="rule rule-top"></div>
    <div class="contact-band">
      <p class="person-name">Owen Whitby</p>
      <p class="person-role">Managing Director</p>
      <p class="phone"><span class="label">phone</span> 0491 726 305</p>
    </div>
    <div class="rule rule-bottom"></div>

    <p class="footer-contacts">
      <span class="label">email</span> brightvolleyracquets@mailbox.example
      <span class="divider">|</span>
      <span class="label">web</span> www.brightvolleyracquets.com.au
    </p>
  </div>
</body>
</html>
```